VOMRA Pty Ltd Business Card

Looking for a simple yet eye-catching double-sided business card design using my company logo on one side and contact details on the other.

Target Market(s)

Government

Industry/Entity Type

Communication Systems Engineering

Contact Information for Business Card

VOMRA Pty Ltd

Requirements
Nice to have
• Would be great to have a QR code so details can be scanned into contacts

```html
<!DOCTYPE html>
<html lang="en">
<head>
<meta charset="utf-8">
<title>VOMRA Pty Ltd Business Card</title>
<link href="https://fonts.googleapis.com/css2?family=Open+Sans:wght@400;600;700&display=swap" rel="stylesheet">
<style>
  :root {
    --slate: #37414a;
    --paper: #ffffff;
    --stage: #e9eaec;
    --ink: #2f3840;
  }
  * { box-sizing: border-box; margin: 0; padding: 0; }
  html, body { width: 1200px; height: 780px; overflow: hidden; }
  body {
    background: var(--stage);
    font-family: "Open Sans", sans-serif;
    position: relative;
  }
  .card {
    position: absolute;
    top: 235px;
    width: 540px;
    height: 310px;
    overflow: hidden;
    box-shadow: 0 6px 18px rgba(0,0,0,0.18);
  }
  .card-front { left: 40px; background: var(--slate); }
  .card-back { left: 620px; background: var(--paper); }

  .brand {
    position: absolute;
    display: flex;
    align-items: center;
    gap: 18px;
  }
  .brand-dot { border-radius: 50%; }
  .brand-name { font-weight: 700; letter-spacing: 4px; line-height: 1; }

  .card-front .brand { left: 0; right: 0; top: 0; bottom: 0; justify-content: center; }
  .card-front .brand-dot { width: 70px; height: 70px; border: 3px solid var(--paper); }
  .card-front .brand-name { color: var(--paper); font-size: 64px; }

  .card-back .brand { left: 150px; top: 30px; }
  .card-back .brand-dot { width: 56px; height: 56px; border: 3px solid var(--ink); }
  .card-back .brand-name { color: var(--ink); font-size: 50px; }

  .holder {
    position: absolute;
    right: 280px;
    top: 140px;
    text-align: right;
    color: var(--ink);
  }
  .holder-name { font-weight: 700; font-size: 22px; line-height: 1.1; }
  .holder-role { font-weight: 600; font-size: 13px; }

  .divider {
    position: absolute;
    left: 276px;
    top: 120px;
    width: 2px;
    height: 72px;
    background: var(--ink);
  }

  .contacts {
    position: absolute;
    left: 292px;
    top: 116px;
    list-style: none;
    color: var(--ink);
    font-size: 14px;
  }
  .contacts li { display: flex; align-items: center; gap: 8px; height: 22px; }
  .contacts svg { width: 13px; height: 13px; fill: var(--ink); }

  .band { position: absolute; left: 0; bottom: 0; width: 540px; height: 310px; }
  .address {
    position: absolute;
    left: 0; right: 0;
    bottom: 12px;
    text-align: center;
    color: var(--paper);
    font-size: 14px;
    letter-spacing: 0.3px;
  }
</style>
</head>
<body>
  <section class="card card-front">
    <div class="brand">
      <span class="brand-dot"></span>
      <span class="brand-name">VOMRA</span>
    </div>
  </section>

  <section class="card card-back">
    <svg class="band" viewBox="0 0 540 310" aria-hidden="true">
      <path d="M0,310 L0,268 Q330,250 540,190 L540,310 Z" fill="#37414a"/>
      <path d="M20,256 Q320,238 520,175" fill="none" stroke="#37414a" stroke-width="3" stroke-linecap="round"/>
    </svg>

    <div class="brand">
      <span class="brand-dot"></span>
      <span class="brand-name">VOMRA</span>
    </div>

    <div class="holder">
      <p class="holder-name">Daniel Morrow</p>
      <p class="holder-role">Co-Founder</p>
    </div>

    <span class="divider"></span>

    <ul class="contacts">
      <li>
        <svg viewBox="0 0 24 24"><path d="M6.6 10.8a15.1 15.1 0 0 0 6.6 6.6l2.2-2.2c.3-.3.7-.4 1-.2 1.1.4 2.3.6 3.6.6.6 0 1 .4 1 1V20c0 .6-.4 1-1 1A17 17 0 0 1 3 4c0-.6.4-1 1-1h3.5c.6 0 1 .4 1 1 0 1.3.2 2.5.6 3.6.1.3 0 .7-.2 1z"/></svg>
        <span>(817) 555-0142</span>
      </li>
      <li>
        <svg viewBox="0 0 24 24"><path d="M12 2a10 10 0 1 0 0 20 10 10 0 0 0 0-20zm6.9 6h-3a15.6 15.6 0 0 0-1.3-3.6A8 8 0 0 1 18.9 8zM12 4c.8 1.2 1.5 2.5 1.9 4h-3.8c.4-1.5 1.1-2.8 1.9-4zM4.3 14a8 8 0 0 1 0-4h3.4a16 16 0 0 0 0 4zm.8 2h3a15.6 15.6 0 0 0 1.3 3.6A8 8 0 0 1 5.1 16zM8 8H5.1a8 8 0 0 1 4.3-3.6C8.8 5.5 8.4 6.7 8 8zm4 12c-.8-1.2-1.5-2.5-1.9-4h3.8c-.4 1.5-1.1 2.8-1.9 4zm2.3-6H9.7a14 14 0 0 1 0-4h4.6a14 14 0 0 1 0 4zm.3 5.6c.6-1.1 1-2.3 1.3-3.6h3a8 8 0 0 1-4.3 3.6zm1.7-5.6a16 16 0 0 0 0-4h3.4a8 8 0 0 1 0 4z"/></svg>
        <span>www.vomra.com.au</span>
      </li>
      <li>
        <svg viewBox="0 0 24 24"><path d="M20 4H4a2 2 0 0 0-2 2v12a2 2 0 0 0 2 2h16a2 2 0 0 0 2-2V6a2 2 0 0 0-2-2zm0 4-8 5-8-5V6l8 5 8-5z"/></svg>
        <span>admin@vomra.com.au</span>
      </li>
    </ul>

    <p class="address">42-44 Harlow Street Westmere NSW 2099 Australia</p>
  </section>
</body>
</html>
```